Wordpress website design for a high-end painting business

We are currently rebranding and are looking to update our Wordpress theme. We have recently rebranded our logo on PixelHarbor, and would like our website to be equally as refined.
Our business is named “Fenwick Painters”. We are a high-end painting business that is known for being professional and having high standards. Our clean and professional image is important as it separates us from our competition. Our current website can be found at www.fenwickcoatings.co.nz . We designed the site ourselves so it is understandably rudimentary. We are generally happy with the. page layout of our existing site, but we like a professional remodel. Any ideas on improvement welcomed.
We would like the front page of the website to summarise all of the info throughout the whole website (I.e introduction, photos, testimonials, contact info etc.) as visitors typically scroll through the first page to see that we are reputable and get to our contact number/email contact at the bottom of the page. We would like this first page to give a clean well rounded image of our business. We would like the gallery to be a scroll through of large photos, as it is difficult to see paint details in smaller photos. A contact page with an enquiry section would also be good.
For the colour scheme, we would like something that fits a bold, masculine and high end theme (similar to our logo attached).
We would like the footer to include Velmora paint logos and the accredited painter logo we have included as these are important to our profession.
We have attached some photos of our work also. I will add more in the coming days. More can also be found on our website.
If you have questions or comments, please don’t hesitate to ask and I will get back as soon as possible.
We are open to your own interpretation or ideas for a better layout/site provided they fit the general brief of being a well rounded site for our profession.
Thanks,
Fenwick Painters.
Target Market(s)
High end clients
Industry/Entity Type
Painting (interior and exterior)
Coding
Coded - Design and coding required
Requirements
Must have
- Classy feel, separating us from typical painting companies. Well rounded homepage.
Nice to have
- Lots of examples of our work
Should not have
- Untidy paint motifs (eg, paint droplets, paint splashes)

```html
<!DOCTYPE html>
<html lang="en">
<head>
<meta charset="utf-8">
<title>Fenwick Painters</title>
<link href="https://fonts.googleapis.com/css2?family=Lora:wght@600;700&family=Roboto:wght@400;500;700&display=swap" rel="stylesheet">
<style>
:root{
  --ink:#1f2631;
  --ink-2:#2a3240;
  --gold:#7b5c39;
  --gold-light:#a5835a;
  --brown-bg:#6c5133;
  --text:#444a52;
  --muted:#7a7f86;
  --light:#f1f2f4;
  --white:#ffffff;
  --star:#f0b429;
}
*{box-sizing:border-box;margin:0;padding:0}
html,body{width:1200px;height:3785px;overflow:hidden}
body{position:relative;font-family:'Roboto',sans-serif;color:var(--text);background:var(--white)}
.abs{position:absolute}
.serif{font-family:'Lora',serif}
.topbar{left:0;top:0;width:1200px;height:47px;background:var(--ink);color:#dfe2e7;font-size:13px}
.topbar .mail{left:112px;top:15px;display:flex;gap:12px;align-items:center}
.topbar .phone{right:112px;top:13px;font-size:16px;font-weight:500;display:flex;gap:12px;align-items:center;color:#fff}
.nav{left:0;top:47px;width:1200px;height:62px;background:var(--white);box-shadow:0 1px 4px rgba(0,0,0,.08)}
.nav a{position:absolute;top:24px;font-size:13px;font-weight:700;color:var(--ink);text-decoration:none;letter-spacing:.2px}
.nav a.active{color:var(--gold);border-bottom:2px solid var(--gold);padding-bottom:3px}
.brand{left:527px;top:2px;width:146px;height:146px;border-radius:50%;background:var(--white);display:flex;flex-direction:column;align-items:center;justify-content:center;z-index:5;box-shadow:0 2px 6px rgba(0,0,0,.12)}
.brand .dot{width:52px;height:52px;border-radius:50%;background:var(--ink);margin-bottom:8px}
.brand b{font-family:'Lora',serif;font-size:17px;color:var(--ink);letter-spacing:.5px;line-height:1}
.brand small{font-family:'Lora',serif;font-size:10px;color:var(--ink);letter-spacing:2px;margin-top:3px}
.hero{left:0;top:109px;width:1200px;height:557px;background:linear-gradient(100deg,#1e242e 0%,#2b323d 55%,#232a34 100%)}
.hero-art{left:573px;top:45px;width:544px;height:434px;border-radius:8px;background:radial-gradient(ellipse at 60% 45%,rgba(200,202,206,.45),rgba(200,202,206,.08) 70%,transparent)}
.hero .kicker{left:112px;top:136px;color:#fff;font-size:21px;letter-spacing:.5px}
.hero h1{left:112px;top:170px;color:#fff;font-size:47px;letter-spacing:.5px;font-weight:700}
.hero .rule{left:112px;top:240px;width:196px;height:6px;background:#fff;clip-path:polygon(0 40%,100% 0,100% 100%,0 70%)}
.hero p{left:112px;top:276px;width:470px;color:#fff;font-size:14px;font-weight:500;line-height:23px}
.btn{display:flex;align-items:center;justify-content:center;gap:10px;background:var(--gold);color:#fff;font-size:13px;font-weight:700;border-radius:3px;letter-spacing:.2px}
.hero .btn{left:112px;top:371px;width:162px;height:47px}
.round-arrow{width:36px;height:36px;border-radius:50%;background:#fff;display:flex;align-items:center;justify-content:center}
.section-label{width:1200px;left:0;text-align:center;font-family:'Lora',serif;font-size:14px;font-weight:700;color:var(--ink);letter-spacing:.5px}
.section-label span::before,.section-label span::after{content:"";display:inline-block;width:44px;height:2px;background:currentColor;vertical-align:middle;margin:0 8px}
.section-title{width:1200px;left:0;text-align:center;font-family:'Lora',serif;font-size:31px;font-weight:700;color:var(--ink);letter-spacing:.5px}
.service{width:362px;height:362px;border-radius:50%;overflow:hidden;border:8px solid #fff;top:855px}
.service .photo{position:absolute;inset:0}
.service .cap{position:absolute;left:0;right:0;top:270px;height:92px;background:rgba(25,30,38,.72);color:#fff;text-align:center;font-family:'Lora',serif;font-size:15px;font-weight:700;padding-top:20px;letter-spacing:.4px}
.service .go{position:absolute;left:151px;top:330px;width:56px;height:56px;border-radius:50%;background:var(--gold);display:flex;justify-content:center;padding-top:10px}
.slide-btn{width:48px;height:26px;border:1px solid #c9ccd1;display:flex;align-items:center;justify-content:center;background:#fff}
.about{left:0;top:1371px;width:1200px;height:514px;background:linear-gradient(90deg,#232a35,#2c3441)}
.about-img{left:133px;top:40px;width:410px;height:410px;border-radius:50%;background:radial-gradient(circle at 50% 40%,#bfa887,#7c8a6a 60%,#4d5c44)}
.about .label{left:617px;top:59px;color:#fff;font-family:'Lora',serif;font-size:14px;font-weight:700}
.about .label::before,.about .label::after{content:"";display:inline-block;width:44px;height:2px;background:#fff;vertical-align:middle;margin:0 8px}
.about .label::before{margin-left:0}
.about h2{left:617px;top:83px;color:#fff;font-family:'Lora',serif;font-size:29px;font-weight:700}
.about p{left:617px;width:473px;color:#e4e7eb;font-size:14px;line-height:25.7px;text-align:justify}
.about .btn{left:617px;top:405px;width:163px;height:47px}
.tile{overflow:hidden}
.tile-info{background:rgba(31,38,49,.9);display:flex;flex-direction:column;align-items:center;text-align:center;padding-top:78px;color:#fff}
.tile-info .zoom{width:34px;height:30px;background:var(--gold);display:flex;align-items:center;justify-content:center;margin-bottom:20px}
.tile-info h3{font-size:18px;font-weight:500;margin-bottom:18px}
.tile-info p{font-size:14px;line-height:21px;width:310px;color:#e8eaee}
.testi{left:0;top:2913px;width:1200px;height:549px;background:linear-gradient(120deg,#75593a,#664c30 50%,#705538)}
.card{top:185px;width:315px;height:298px;background:#fff;padding:55px 26px 0;box-shadow:0 6px 18px rgba(0,0,0,.2)}
.card.dark{background:var(--ink);color:#fff}
.card .q{position:absolute;left:25px;top:-25px;width:50px;height:50px;border-radius:50%;background:var(--ink);color:#fff;font-family:'Lora',serif;font-size:40px;display:flex;justify-content:center;line-height:68px;border:3px solid #fff}
.card.dark .q{background:var(--gold);border-color:var(--ink)}
.card .date{font-size:13px;font-weight:500;color:var(--ink)}
.card.dark .date{color:#fff}
.card p{margin-top:22px;font-size:12.5px;line-height:22px;color:var(--muted);text-align:justify}
.card.dark p{color:#e4e7eb}
.card .who{position:absolute;left:26px;top:232px;display:flex;align-items:center;gap:22px}
.card .avatar{width:52px;height:52px;border-radius:50%;background:linear-gradient(#c9ced6,#8d96a3)}
.card .name{font-size:13px;font-weight:700;color:var(--ink)}
.card.dark .name{color:#fff}
.card .stars{color:var(--star);font-size:12px;letter-spacing:1px}
.sq-arrow{width:46px;height:34px;background:var(--ink);display:flex;align-items:center;justify-content:center}
.footer{left:0;top:3462px;width:1200px;height:323px;background:var(--light)}
.footer .links{left:0;top:70px;width:1200px;display:flex;justify-content:center;gap:22px;font-size:14px;font-weight:700;color:var(--ink)}
.footer .links i{font-style:normal;color:#777;font-weight:400}
.footer .rule{left:112px;top:114px;width:976px;height:1px;background:#d6d8dc}
.foot-brand{left:112px;top:148px;display:flex;flex-direction:column;align-items:center;width:116px}
.foot-brand .dot{width:64px;height:64px;border-radius:50%;background:var(--ink);margin-bottom:8px}
.foot-brand b{font-family:'Lora',serif;font-size:17px;color:var(--ink);line-height:1}
.foot-brand small{font-family:'Lora',serif;font-size:10px;letter-spacing:2px;color:var(--ink)}
.footer h4{font-size:13px;font-weight:700;color:var(--ink);letter-spacing:.4px}
.footer .line{display:flex;gap:14px;align-items:flex-start;font-size:13px;color:var(--ink);line-height:22px}
.social{width:34px;height:34px;border:1px solid #c9ccd1;background:#fff}
.badge{left:833px;top:277px;width:257px;height:23px;display:flex;gap:4px}
</style>
</head>
<body>

<div class="abs topbar">
  <div class="abs mail">
    <svg width="14" height="11" viewBox="0 0 14 11"><rect width="14" height="11" rx="1" fill="#dfe2e7"/><path d="M0 1l7 5 7-5" stroke="#1f2631" stroke-width="1.4" fill="none"/></svg>
    hello@fenwickpainters.co.nz
  </div>
  <div class="abs phone">
    <svg width="14" height="14" viewBox="0 0 24 24"><path fill="#fff" d="M6.6 10.8a15 15 0 006.6 6.6l2.2-2.2a1 1 0 011-.25 11.4 11.4 0 003.6.57 1 1 0 011 1V20a1 1 0 01-1 1A17 17 0 013 4a1 1 0 011-1h3.5a1 1 0 011 1c0 1.250.2 2.45.57 3.57a1 1 0 01-.25 1z"/></svg>
    022 555 0147
  </div>
</div>

<nav class="abs nav">
  <a class="active" style="left:112px">HOME</a>
  <a style="left:201px">ABOUT</a>
  <a style="left:295px">OUR SERVICES</a>
  <a style="left:763px">GALLERY</a>
  <a style="left:872px">TESTIMONIALS</a>
  <a style="left:1022px">CONTACT</a>
</nav>

<div class="abs brand"><span class="dot"></span><b>FENWICK</b><small>PAINTERS</small></div>

<section class="abs hero">
  <div class="abs hero-art" role="img" aria-label="Large pale line illustration of an archer drawing a bow"></div>
  <div class="abs kicker serif">WELCOME TO</div>
  <h1 class="abs serif">FENWICK PAINTERS</h1>
  <div class="abs rule"></div>
  <p class="abs">Here at Fenwick Painters, we take a lot of pride in our work. We strive to ensure the highest quality paint-work, paying close attention to detail to provide a long lasting finish.</p>
  <div class="abs btn">GET STARTED
    <svg width="13" height="13" viewBox="0 0 14 14"><circle cx="7" cy="7" r="7" fill="#fff"/><path d="M5.5 4l3 3-3 3" stroke="#7b5c39" stroke-width="1.8" fill="none"/></svg></div>
  <div class="abs round-arrow" style="left:33px;top:261px"><svg width="10" height="14" viewBox="0 0 10 14"><path d="M7 2L2 7l5 5" stroke="#1f2631" stroke-width="2" fill="none"/></svg></div>
  <div class="abs round-arrow" style="left:1129px;top:261px"><svg width="10" height="14" viewBox="0 0 10 14"><path d="M3 2l5 5-5 5" stroke="#1f2631" stroke-width="2" fill="none"/></svg></div>
</section>

<div class="abs section-label" style="top:745px"><span>WHAT WE DO</span></div>
<h2 class="abs section-title" style="top:768px">OUR SERVICES</h2>

<div class="abs service" style="left:103px">
  <div class="photo" role="img" aria-label="White weatherboard house exterior under a blue sky" style="background:linear-gradient(#7ea6d6 0%,#c9d7e6 40%,#e8e8e4 55%,#5d7a3e 100%)"></div>
  <div class="cap">EXTERIOR PAINTING</div>
  <div class="go"><svg width="14" height="14" viewBox="0 0 14 14"><path d="M1 7h11M8 3l4 4-4 4" stroke="#fff" stroke-width="2" fill="none"/></svg></div>
</div>
<div class="abs service" style="left:418px">
  <div class="photo" role="img" aria-label="Freshly painted empty interior room" style="background:linear-gradient(#d9d5ce,#bfb8ad 60%,#8c7d68)"></div>
  <div class="cap">INTERIOR PAINTING</div>
  <div class="go"><svg width="14" height="14" viewBox="0 0 14 14"><path d="M1 7h11M8 3l4 4-4 4" stroke="#fff" stroke-width="2" fill="none"/></svg></div>
</div>
<div class="abs service" style="left:730px">
  <div class="photo" role="img" aria-label="Feature wall with green patterned wallpaper" style="background:linear-gradient(90deg,#d6d6d2 0%,#5b6556 25%,#4e594b 70%,#dcdedb 100%)"></div>
  <div class="cap">WALLPAPERING</div>
  <div class="go"><svg width="14" height="14" viewBox="0 0 14 14"><path d="M1 7h11M8 3l4 4-4 4" stroke="#fff" stroke-width="2" fill="none"/></svg></div>
</div>

<div class="abs slide-btn" style="left:549px;top:1280px"><svg width="22" height="10" viewBox="0 0 22 10"><path d="M21 5H2M6 1L2 5l4 4" stroke="#1f2631" stroke-width="1.5" fill="none"/></svg></div>
<div class="abs slide-btn" style="left:603px;top:1280px"><svg width="22" height="10" viewBox="0 0 22 10"><path d="M1 5h19M16 1l4 4-4 4" stroke="#1f2631" stroke-width="1.5" fill="none"/></svg></div>

<section class="abs about">
  <div class="abs about-img" role="img" aria-label="Two-storey rendered family home with garden, framed in a circle"></div>
  <div class="abs label">ABOUT US</div>
  <h2 class="abs">WHO WE ARE</h2>
  <p class="abs" style="top:132px">Here at Fenwick Painters, we take a lot of pride in our work. We strive to ensure the highest quality paint-work, paying close attention to detail to provide a long lasting finish. Our clients are always our priority, we aim to deliver beyond their expectations. It is our goal to provide an excellent service from start to finish through clear communication, free quoting and transparency with our pricing.</p>
  <p class="abs" style="top:312px">We take great pride in the preparation of surfaces for painting and only use the best quality products to ensure we achieve the best finish for you. Our qualified interior designer can also assist you</p>
  <div class="abs btn">LEARN MORE
    <svg width="13" height="13" viewBox="0 0 14 14"><circle cx="7" cy="7" r="7" fill="#fff"/><path d="M5.5 4l3 3-3 3" stroke="#7b5c39" stroke-width="1.8" fill="none"/></svg></div>
</section>

<div class="abs section-label" style="top:1973px"><span>PORTFOLIO</span></div>
<h2 class="abs section-title" style="top:1996px">OUR GALLERY</h2>

<div class="abs tile" role="img" aria-label="Bright hallway with white staircase and pendant light" style="left:126px;top:2073px;width:434px;height:320px;background:linear-gradient(#e4e3de,#cfccc4 70%,#6b6158)"></div>
<div class="abs tile" role="img" aria-label="Open-plan living room and kitchen with large windows" style="left:576px;top:2073px;width:495px;height:320px;background:linear-gradient(#ecebe6,#b8b09f 60%,#4b3d32)"></div>
<div class="abs tile" role="img" aria-label="Living room with blue carpet and sofa" style="left:126px;top:2414px;width:271px;height:318px;background:linear-gradient(#e6e3dc,#c7c1b5 60%,#233457)"></div>
<div class="abs tile tile-info" style="left:411px;top:2414px;width:372px;height:318px">
  <div class="zoom"><svg width="14" height="14" viewBox="0 0 14 14"><circle cx="6" cy="6" r="4" stroke="#fff" stroke-width="1.8" fill="none"/><path d="M9 9l4 4" stroke="#fff" stroke-width="1.8"/></svg></div>
  <h3>Lorem ipsum dolor sit amet</h3>
  <p>Sed ut perspiciatis unde omnis iste natus error sit voluptatem accusantium doloremque laudantium, totam rem aperiam</p>
</div>
<div class="abs tile" role="img" aria-label="Garage interior with white ceiling and grey roller door" style="left:801px;top:2414px;width:270px;height:318px;background:linear-gradient(#e8e8e6,#9a9c9c 55%,#5e6062)"></div>

<div class="abs btn" style="left:497px;top:2773px;width:205px;height:47px">VIEW ALL PORTFOLIO
  <svg width="13" height="13" viewBox="0 0 14 14"><circle cx="7" cy="7" r="7" fill="#fff"/><path d="M5.5 4l3 3-3 3" stroke="#7b5c39" stroke-width="1.8" fill="none"/></svg></div>

<section class="abs testi">
  <div class="abs section-label" style="top:62px;color:#fff"><span>TESTIMONIALS</span></div>
  <h2 class="abs section-title" style="top:86px;color:#fff">WHAT OUR CLIENTS SAY</h2>

  <div class="abs sq-arrow" style="left:56px;top:317px"><svg width="24" height="12" viewBox="0 0 24 12"><path d="M23 6H2M7 1L2 6l5 5" stroke="#fff" stroke-width="1.8" fill="none"/></svg></div>
  <div class="abs sq-arrow" style="left:1097px;top:317px"><svg width="24" height="12" viewBox="0 0 24 12"><path d="M1 6h21M17 1l5 5-5 5" stroke="#fff" stroke-width="1.8" fill="none"/></svg></div>

  <div class="abs card" style="left:104px">
    <div class="q">“</div>
    <div class="date">MAR 01, 2022</div>
    <p>Just had our house interior painted throughout by Fenwick. They were professional right from the start. They turned up to give a quote when other firms never responded.</p>
    <div class="who"><div class="avatar"></div><div><div class="name">DANIEL MOORE</div><div class="stars">★★★★★</div></div></div>
  </div>
  <div class="abs card dark" style="left:444px">
    <div class="q">“</div>
    <div class="date">MAR 01, 2022</div>
    <p>Liam and his Team have done an amazing job painting our house. Without a doubt hiring them was our best decision. Attention to detail, great communication, respect towards our needs, working within the budget</p>
    <div class="who"><div class="avatar"></div><div><div class="name">MARTA KOWAL</div><div class="stars">★★★★★</div></div></div>
  </div>
  <div class="abs card" style="left:781px">
    <div class="q">“</div>
    <div class="date">MAR 01, 2022</div>
    <p>Lorem ipsum dolor sit amet, consectetur adipiscing elit, sed do eiusmod tempor incididunt ut labore et dolore magna aliqua. Ut enim ad minim veniam, quis nostrud exercitation ullamco laboris</p>
    <div class="who"><div class="avatar"></div><div><div class="name">HANNAH T</div><div class="stars">★★★★★</div></div></div>
  </div>
</section>

<footer class="abs footer">
  <div class="abs links"><span>HOME</span><i>|</i><span>ABOUT</span><i>|</i><span>BENEFITS</span><i>|</i><span>WHY US</span><i>|</i><span>PROCESS</span><i>|</i><span>CONTACT</span></div>
  <div class="abs rule"></div>
  <div class="abs foot-brand"><span class="dot"></span><b>FENWICK</b><small>PAINTERS</small></div>
  <div class="abs" style="left:112px;top:275px;font-size:14px;color:var(--ink)">© 2022 Fenwick Painters. All Rights Reserved</div>

  <h4 class="abs" style="left:439px;top:162px">OFFICE LOCATION</h4>
  <div class="abs line" style="left:439px;top:192px">
    <svg width="10" height="14" viewBox="0 0 10 14" style="margin-top:4px"><path d="M5 0a5 5 0 00-5 5c0 4 5 9 5 9s5-5 5-9a5 5 0 00-5-5z" fill="#1f2631"/><circle cx="5" cy="5" r="2" fill="#f1f2f4"/></svg>
    <div>48 Kowhai Lane<br>Hamilton, Waikato</div>
  </div>

  <h4 class="abs" style="left:733px;top:162px">CONTACT US</h4>
  <div class="abs line" style="left:733px;top:192px;font-size:16px;font-weight:500">
    <svg width="14" height="14" viewBox="0 0 24 24" style="margin-top:4px"><path fill="#1f2631" d="M6.6 10.8a15 15 0 006.6 6.6l2.2-2.2a1 1 0 011-.25 11.4 11.4 0 003.6.57 1 1 0 011 1V20a1 1 0 01-1 1A17 17 0 013 4a1 1 0 011-1h3.5a1 1 0 011 1c0 1.25.2 2.45.57 3.57a1 1 0 01-.25 1z"/></svg>
    022 555 0147
  </div>
  <div class="abs line" style="left:733px;top:222px">
    <svg width="14" height="11" viewBox="0 0 14 11" style="margin-top:6px"><rect width="14" height="11" rx="1" fill="#1f2631"/><path d="M0 1l7 5 7-5" stroke="#f1f2f4" stroke-width="1.4" fill="none"/></svg>
    hello@fenwickpainters.co.nz
  </div>

  <div class="abs social" style="left:981px;top:166px"></div>
  <div class="abs social" style="left:1024px;top:166px"></div>
  <div class="abs social" style="left:981px;top:208px"></div>
  <div class="abs social" style="left:1024px;top:208px"></div>

  <div class="abs badge">
    <div style="width:72px;height:23px;background:#1d2b6b"></div>
    <div style="flex:1;height:23px;background:#1f6fb8"></div>
  </div>
</footer>

</body>
</html>
```